Interior designer needs a power point template design

I need a template PowerPoint design for my client presentations. The presentations I prepare for my clients usually include the furniture project, the detail of the selected furniture, and the costs. There are a lot of images I insert. What I need is to have a template that I can use for all my presentations, where from time to time I will insert the specific images and descriptions I want to insert. What will always be the same will be the cover, the colors, the font, and the design of the internal sections.
I already have my logo that I would like to insert on each page of the presentation (in small size).
In summary, I need:
- basic template design
- cover with an image chosen by Pictavale photo
- design an internal section/chapter
- internal page design.

I like the clolors of pink and brown <8please see image attached)
Images (will come from Pictavale photo)
● entrance/hall
● living room
● dining room
● Bathroom
● Closet
● Kids room
● Master bedroom
● Master bathroom
● Kitchen
● Office
● Laundry
● Balcony or Terrace

Target Market(s)

Customers (both residential and commercial projects)

Industry/Entity Type

interior design

Font styles to use
Other font styles liked:
• I like courier new

Requirements
Must have
• beautiful design
Should not have
• animations

```html
<!DOCTYPE html>
<html lang="it">
<head>
<meta charset="utf-8">
<title>Stanza Nuova – Presentation Template</title>
<link href="https://fonts.googleapis.com/css2?family=Audiowide&family=Lato:wght@300;400&display=swap" rel="stylesheet">
<style>
:root{
  --canvas:#7e8081;
  --white:#ffffff;
  --terracotta:#b97a67;
  --blush:#ead3cc;
  --brown:#7a3a1c;
  --ink:#1e1e1e;
  --body:#6f6f6f;
  --dot:#b98273;
  --line:#bdbdbd;
}
*{margin:0;padding:0;box-sizing:border-box}
html,body{width:1200px;height:3827px;overflow:hidden;background:var(--canvas)}
body{position:relative;font-family:'Lato',sans-serif}
.slide{position:absolute;left:116px;width:968px;height:544px;background:var(--white);overflow:hidden}
.abs{position:absolute}
.brand-tab{position:absolute;right:0;top:0;width:60px;height:93px;background:var(--white);display:flex;flex-direction:column;align-items:center;padding-top:8px;gap:6px;z-index:5}
.brand-tab .mark{width:38px;height:38px;border:1px solid #999;border-radius:50%}
.brand-tab .name{font-family:'Lato',sans-serif;font-weight:300;font-size:10px;line-height:11px;letter-spacing:1px;color:#555;text-align:center}
.label{font-family:'Audiowide',sans-serif;font-size:15px;color:var(--brown)}
.title{font-family:'Audiowide',sans-serif;font-size:29px;line-height:34px;color:var(--ink)}
.subhead{font-family:'Audiowide',sans-serif;font-size:17px;color:var(--ink)}
.copy{font-size:9.6px;line-height:15.2px;color:var(--body);text-align:justify}
.photo{position:absolute;border-radius:12px}
.dots{position:absolute;display:grid;gap:11px}
.dots span{width:5px;height:5px;border-radius:50%;background:var(--dot)}
.dots.light span{background:#d9cfcb}
.dots.dark span{background:var(--brown)}
.on-terra .title,.on-terra .copy{color:var(--white)}
.contact{position:absolute;left:576px;display:flex;align-items:flex-start;gap:14px;color:var(--white);font-size:13.5px;line-height:20px}
.contact svg{width:14px;height:14px;margin-top:3px;fill:var(--white);flex:none}
.cover-diamond{position:absolute;left:113px;top:129px;width:315px;height:315px;transform:rotate(45deg);background:var(--white)}
.cover-outline{position:absolute;left:112px;top:118px;width:330px;height:330px;transform:rotate(45deg);border:1px solid rgba(255,255,255,.85)}
.cover-text{position:absolute;left:120px;width:300px;text-align:center}
</style>
</head>
<body>

<!-- Cover -->
<section class="slide" style="top:107px">
  <div class="abs" role="img" aria-label="Illustrated kitchen interior at sunset" style="inset:0;background:linear-gradient(160deg,#7a4d78 0%,#a6707a 35%,#c97a5c 60%,#a8314a 85%,#7e1b2b 100%)"></div>
  <div class="cover-outline"></div>
  <div class="cover-diamond"></div>
  <div class="cover-text label" style="top:194px">Welcome To</div>
  <div class="cover-text title" style="top:216px">Stanza Nuova<br>Interior Design</div>
  <p class="copy" style="position:absolute;left:150px;top:292px;width:240px;text-align:center;font-size:8.6px;line-height:15px">Lorem ipsum dolor sit amet, consectetur adipiscing elit, sed do eiusmod tempor incididunt ut labore et dolore magna aliqua. Quis ipsum suspendisse ultrices gravida. Risus commodo viverra maecenas accumsan lacus vel facilisis. Lorem ipsum dolor sit amet, consectetur adipiscing elit.</p>
  <div class="brand-tab"><div class="mark"></div><div class="name">STANZA<br>NUOVA</div></div>
</section>

<!-- Master bedroom -->
<section class="slide" style="top:714px">
  <div class="abs" style="left:0;top:0;width:100px;height:110px;background:var(--blush)"></div>
  <div class="dots light" style="left:427px;top:10px;grid-template-columns:repeat(6,5px)">
    <span></span><span></span><span></span><span></span><span></span><span></span>
    <span></span><span></span><span></span><span></span><span></span><span></span>
    <span></span><span></span><span></span><span></span><span></span><span></span>
    <span></span><span></span><span></span><span></span><span></span><span></span>
  </div>
  <div class="label abs" style="left:58px;top:106px">Camera padronale</div>
  <div class="title abs" style="left:58px;top:128px">L’arredamento<br>della camera padronale</div>
  <p class="copy abs" style="left:58px;top:205px;width:414px">Lorem ipsum dolor sit amet, consectetur adipiscing elit, sed do eiusmod tempor incididunt ut labore et dolore magna aliqua. Quis ipsum suspendisse ultrices gravida. Risus commodo viverra maecenas accumsan lacus vel facilisis. Lorem ipsum dolor sit amet, consectetur adipiscing elit. Lorem ipsum dolor sit amet, consectetur adipiscing elit, sed do eiusmod tempor incididunt ut labore et dolore magna aliqua. Quis ipsum suspendisse ultrices gravida. Risus commodo viverra maecenas accumsan lacus vel facilisis. Lorem ipsum dolor sit amet, consectetur adipiscing elit. Lorem ipsum dolor sit amet, consectetur adipiscing elit, sed do eiusmod tempor incididunt ut labore et dolore magna aliqua. Quis ipsum suspendisse ultrices</p>
  <div class="subhead abs" style="left:56px;top:360px">Lorem Ipsum</div>
  <p class="copy abs" style="left:56px;top:390px;width:416px">Lorem ipsum dolor sit amet, consectetur adipiscing elit, sed do eiusmod tempor incididunt ut labore et dolore magna aliqua. Quis ipsum suspendisse ultrices gravida. Risus commodo viverra maecenas accumsan lacus vel facilisis. Lorem ipsum dolor sit amet, consectetur adipiscing elit, sed do eiusmod tempor Lorem ipsum dolor sit amet, consectetur adipiscing elit, sed do eiusmod tempor</p>
  <div class="photo" role="img" aria-label="Master bedroom with chandelier, dark bed and open wardrobe" style="left:505px;top:37px;width:395px;height:457px;background:linear-gradient(180deg,#9ea1a3 0%,#c9cccd 45%,#3f454b 68%,#8a5a33 100%)"></div>
  <div class="dots dark" style="left:760px;top:497px;grid-template-columns:repeat(6,5px);gap:13px 14px">
    <span></span><span></span><span></span><span></span><span></span><span></span>
    <span></span><span></span><span></span><span></span><span></span><span></span>
  </div>
  <div class="brand-tab"><div class="mark"></div><div class="name">STANZA<br>NUOVA</div></div>
</section>

<!-- Closet -->
<section class="slide" style="top:1326px">
  <div class="abs" style="left:0;top:190px;width:456px;height:354px;background:var(--terracotta)"></div>
  <div class="abs" style="left:310px;top:500px;width:146px;height:44px;background:var(--white)"></div>
  <div class="dots" style="left:4px;top:6px;grid-template-columns:repeat(7,5px);gap:12px 12px">
    <span></span><span></span><span></span><span></span><span></span><span></span><span></span>
    <span></span><span></span><span></span><span></span><span></span><span></span><span></span>
    <span></span><span></span><span></span><span></span><span></span><span></span><span></span>
    <span></span><span></span><span></span><span></span><span></span><span></span><span></span>
  </div>
  <div class="photo" role="img" aria-label="Walk-in closet with hanging clothes and drawers" style="left:60px;top:43px;width:396px;height:456px;background:linear-gradient(180deg,#bfbfbf 0%,#4a4e5a 20%,#7a6a58 35%,#d0d0d0 45%,#3b3f4a 60%,#8d7a66 72%,#d5d5d5 85%,#c6c6c6 100%)"></div>
  <div class="dots" style="left:336px;top:488px;grid-template-columns:repeat(6,5px);gap:13px 13px">
    <span></span><span></span><span></span><span></span><span></span><span></span>
    <span></span><span></span><span></span><span></span><span></span><span></span>
    <span></span><span></span><span></span><span></span><span></span><span></span>
  </div>
  <div class="label abs" style="left:491px;top:106px">Cabina armadio</div>
  <div class="title abs" style="left:491px;top:128px">Lorem ipsum dolor sit<br>amet, consectetur</div>
  <p class="copy abs" style="left:490px;top:205px;width:414px">Lorem ipsum dolor sit amet, consectetur adipiscing elit, sed do eiusmod tempor incididunt ut labore et dolore magna aliqua. Quis ipsum suspendisse ultrices gravida. Risus commodo viverra maecenas accumsan lacus vel facilisis. Lorem ipsum dolor sit amet, consectetur adipiscing elit. Lorem ipsum dolor sit amet, consectetur adipiscing elit, sed do eiusmod tempor incididunt ut labore et dolore magna aliqua. Quis ipsum suspendisse ultrices gravida. Risus commodo viverra maecenas accumsan lacus vel facilisis. Lorem ipsum dolor sit amet, consectetur adipiscing elit. Lorem ipsum dolor sit amet, consectetur adipiscing elit, sed do eiusmod tempor incididunt ut labore et dolore magna aliqua. Quis ipsum suspendisse ultrices</p>
  <div class="subhead abs" style="left:488px;top:363px">Lorem Ipsum</div>
  <p class="copy abs" style="left:488px;top:388px;width:416px">Lorem ipsum dolor sit amet, consectetur adipiscing elit, sed do eiusmod tempor incididunt ut labore et dolore magna aliqua. Quis ipsum suspendisse ultrices gravida. Risus commodo viverra maecenas accumsan lacus vel facilisis. Lorem ipsum dolor sit amet, consectetur adipiscing elit, sed do eiusmod tempor Lorem ipsum dolor sit amet, consectetur adipiscing elit, sed do eiusmod tempor</p>
  <div class="abs" style="left:904px;top:472px;width:64px;height:72px;background:var(--terracotta)"></div>
  <div class="brand-tab"><div class="mark"></div><div class="name">STANZA<br>NUOVA</div></div>
</section>

<!-- Section divider: master bathroom -->
<section class="slide on-terra" style="top:1941px;background:var(--terracotta)">
  <div class="abs" role="img" aria-label="Illustrated living room with red sofa, bookcase, plants and window" style="left:0;top:0;width:968px;height:297px;background:linear-gradient(180deg,#bfe9e6 0%,#a7dcda 70%,#6e7d92 88%,#4f5f78 100%);border-radius:0 0 14px 14px"></div>
  <div class="label abs" style="left:382px;top:320px">Bagno padronale</div>
  <div class="title abs" style="left:382px;top:342px;color:var(--white)">Lorem ipsum dolor sit amet<br>consectetur</div>
  <p class="copy abs" style="left:382px;top:422px;width:514px">Lorem ipsum dolor sit amet, consectetur adipiscing elit, sed do eiusmod tempor incididunt ut labore et dolore magna aliqua. Quis ipsum suspendisse ultrices gravida. Risus commodo viverra maecenas accumsan lacus vel facilisis. Lorem ipsum dolor sit amet, consectetur adipiscing elit. Lorem ipsum dolor sit amet, consectetur adipiscing elit, sed do eiusmod tempor incididunt ut labore et dolore magna aliqua. Quis ipsum suspendisse ultrices gravida. Risus commodo viverra maecenas accumsan lacus vel facilisis. Lorem ipsum dolor sit amet, consectetur adipiscing elit. Lorem ipsum dolor sit amet.</p>
  <div class="brand-tab"><div class="mark"></div><div class="name">STANZA<br>NUOVA</div></div>
</section>

<!-- Master bathroom gallery -->
<section class="slide" style="top:2550px">
  <div class="abs" style="left:0;top:272px;width:632px;height:272px;background:var(--terracotta)"></div>
  <div class="label abs" style="left:46px;top:27px">Bagno padronale</div>
  <div class="title abs" style="left:46px;top:48px">Lorem ipsum dolor sit<br>amet consectetur</div>
  <div class="abs" role="img" aria-label="Bathroom with freestanding tub, chandelier and patterned tiles" style="left:43px;top:132px;width:290px;height:412px;background:linear-gradient(180deg,#2b2f33 0%,#3a3e42 35%,#d9dadb 50%,#cfd0d1 72%,#3c3c3c 85%,#e6e6e6 100%)"></div>
  <div class="abs" role="img" aria-label="Illustrated kids room with toys and shelves" style="left:420px;top:30px;width:276px;height:276px;background:linear-gradient(135deg,#e9643b 0%,#b8c24a 45%,#8fa538 70%,#c9a15b 100%)"></div>
  <div class="subhead abs" style="left:718px;top:100px;font-size:16px">Lorem Ipsum</div>
  <p class="copy abs" style="left:718px;top:128px;width:210px">Lorem ipsum dolor sit amet, consectetur adipiscing elit, sed do eiusmod tempor incididunt ut labore et dolore magna aliqua. Quis ipsum suspendisse ultrices gravida. Risus commodo viverra maecenas accumsan lacus vel facilisis. Lorem ipsum dolor Lorem ipsum dolor sit amet, consectetur adipiscing elit, sed do eiusmod tempor</p>
  <p class="copy abs" style="left:361px;top:362px;width:246px;color:var(--white)">Lorem ipsum dolor sit amet, consectetur adipiscing elit, sed do eiusmod tempor incididunt ut labore et dolore magna aliqua. Quis ipsum suspendisse ultrices gravida. Risus commodo viverra maecenas accumsan lacus vel facilisis. Lorem ipsum dolor sit amet, consectetur adipiscing elit. Lorem ipsum dolor sit amet, consectetur adipiscing elit, sed do eiusmod tempor incididunt ut labore et dolore magna aliqua. Quis ipsum suspendisse ultrices gravida.</p>
  <div class="abs" role="img" aria-label="Clothes rack with pastel garments and plant" style="left:704px;top:327px;width:264px;height:217px;background:linear-gradient(135deg,#d8d2cd 0%,#cfc9c4 40%,#d99a6a 60%,#8fb99a 80%,#c8c2bd 100%)"></div>
  <div class="brand-tab"><div class="mark"></div><div class="name">STANZA<br>NUOVA</div></div>
</section>

<!-- Closing -->
<section class="slide" style="top:3159px;background:var(--terracotta)">
  <div class="abs" role="img" aria-label="Illustrated interior ceiling with hanging lamps" style="left:0;top:0;width:968px;height:119px;background:linear-gradient(180deg,#6b3a2a 0%,#a85a38 50%,#c96f45 100%)"></div>
  <div class="abs" role="img" aria-label="Illustrated floor with oval rug" style="left:0;top:428px;width:968px;height:116px;background:linear-gradient(90deg,#2f6f8a 0%,#c9683d 35%,#d7a45a 55%,#b44a2f 75%,#1f8a6a 100%)"></div>
  <div class="abs" style="left:88px;top:169px;width:142px;height:142px;border:1px solid rgba(255,255,255,.85);border-radius:50%"></div>
  <div class="abs" style="left:262px;top:150px;font-family:'Lato',sans-serif;font-weight:300;font-size:44px;line-height:48px;letter-spacing:4px;color:var(--white)">STANZA<br>NUOVA</div>
  <div class="abs" style="left:190px;top:350px;display:flex;gap:11px">
    <span style="width:28px;height:28px;border:1px solid var(--white);border-radius:50%"></span>
    <span style="width:28px;height:28px;border:1px solid var(--white);border-radius:50%"></span>
    <span style="width:28px;height:28px;border:1px solid var(--white);border-radius:50%"></span>
    <span style="width:28px;height:28px;border:1px solid var(--white);border-radius:50%"></span>
  </div>
  <div class="abs" style="left:499px;top:150px;width:1px;height:253px;background:rgba(255,255,255,.85)"></div>
  <div class="abs" style="left:567px;top:160px;font-family:'Audiowide',sans-serif;font-size:44px;color:var(--white)">Thank You</div>
  <div class="contact" style="top:237px"><svg viewBox="0 0 24 24"><path d="M12 2a7 7 0 0 0-7 7c0 5 7 13 7 13s7-8 7-13a7 7 0 0 0-7-7zm0 9.5A2.5 2.5 0 1 1 12 6.5a2.5 2.5 0 0 1 0 5z"/></svg><span>di Marta Ferrante<br>via dei Tigli, 42</span></div>
  <div class="contact" style="top:289px"><svg viewBox="0 0 24 24"><path d="M6.6 10.8a15.1 15.1 0 0 0 6.6 6.6l2.2-2.2a1 1 0 0 1 1-.25 11.4 11.4 0 0 0 3.6.57 1 1 0 0 1 1 1V20a1 1 0 0 1-1 1A17 17 0 0 1 3 4a1 1 0 0 1 1-1h3.5a1 1 0 0 1 1 1c0 1.25.2 2.45.57 3.6a1 1 0 0 1-.25 1z"/></svg><span>340/5518263</span></div>
  <div class="contact" style="top:331px"><svg viewBox="0 0 24 24"><path d="M12 2a10 10 0 1 0 0 20 10 10 0 0 0 0-20zm6.9 6h-3a15.7 15.7 0 0 0-1.4-3.6A8 8 0 0 1 18.9 8zM12 4a14 14 0 0 1 1.9 4h-3.8A14 14 0 0 1 12 4zM4.3 14a8.2 8.2 0 0 1 0-4h3.4a16.5 16.5 0 0 0 0 4zm.8 2h3a15.7 15.7 0 0 0 1.4 3.6A8 8 0 0 1 5.1 16zm3-8h-3a8 8 0 0 1 4.4-3.6A15.7 15.7 0 0 0 8.1 8zM12 20a14 14 0 0 1-1.9-4h3.8A14 14 0 0 1 12 20zm2.3-6H9.7a14.7 14.7 0 0 1 0-4h4.6a14.7 14.7 0 0 1 0 4zm.2 5.6a15.7 15.7 0 0 0 1.4-3.6h3a8 8 0 0 1-4.4 3.6zm1.8-5.6a16.5 16.5 0 0 0 0-4h3.4a8.2 8.2 0 0 1 0 4z"/></svg><span>www.stanzanuova.it</span></div>
  <div class="contact" style="top:374px"><svg viewBox="0 0 24 24"><path d="M2 5h20v14H2zm2 2v.5l8 5 8-5V7l-8 5z"/></svg><span>marta.ferrante@example.com</span></div>
</section>

</body>
</html>
```